Business card for Luxury Portable Restroom Trailer company

We are a Luxury Portable Restroom Trailer Company Called FALCRIDGE HIRES. Based in Orange County California. We provide portable restroom trailers for events, such as, Weddings, Concerts, Charity events, Sporting events, Tournaments, Corporate events, ect. We rent and Sell the Luxury restrooms. Our colors are white, grey, and Orange. As you will see in the logo we uploaded.
There are 2 people in the company so the names and titles will change for the 3 people but card will remain the same. Here is the information for each Person: Dwight Penner CFO 555 318-0476
next Person: Leon Marchetti VP 555 318-0476
Next Person: Owen Marchetti CEO 555 318-0476
Information to include on the card: Luxury Restroom Trailers Rental and Sales. Weddings, Concerts, Charity, Sporting and Corp. Events.

```html
<!DOCTYPE html>
<html lang="en">
<head>
<meta charset="utf-8">
<title>Falcridge Hires – Business Card</title>
<link rel="stylesheet" href="https://fonts.googleapis.com/css2?family=Montserrat:wght@400;500;700;800&display=swap">
<style>
  :root {
    --orange: #e8601f;
    --orange-light: #ef7a36;
    --orange-deep: #dd5419;
    --grey: #55575a;
    --grey-text: #4a4a4a;
    --white: #ffffff;
    --paper-bg-top: #cfcfcf;
    --paper-bg-bottom: #a9a9a9;
    --faint: #f4f4f4;
  }
  * { box-sizing: border-box; margin: 0; padding: 0; }
  html, body {
    width: 1200px; height: 802px; overflow: hidden;
  }
  body {
    font-family: "Montserrat", sans-serif;
    background: linear-gradient(180deg, var(--paper-bg-top), var(--paper-bg-bottom));
    display: flex; align-items: center; justify-content: center; gap: 48px;
  }
  .card {
    position: relative;
    width: 525px; height: 300px;
    border-radius: 22px;
    overflow: hidden;
    box-shadow: 0 14px 30px rgba(0,0,0,0.28);
  }

  /* Front */
  .card-front { background: var(--white); }
  .front-decoration {
    position: absolute; right: 60px; top: -40px;
    width: 250px; height: 230px;
    border-radius: 50%;
    background: radial-gradient(circle, #f1f1f1 0%, var(--faint) 60%, rgba(255,255,255,0) 72%);
  }
  .brand {
    position: absolute; left: 34px; top: 40px;
    display: flex; align-items: center; gap: 9px;
  }
  .brand-square { width: 14px; height: 14px; background: var(--orange); }
  .brand-name {
    font-weight: 800; font-size: 22px; letter-spacing: 0.5px;
    color: var(--orange);
  }
  .person { position: absolute; left: 34px; top: 132px; }
  .person-name {
    font-weight: 800; font-size: 22px; letter-spacing: 1px;
    color: var(--orange);
  }
  .person-title {
    margin-top: 3px; font-weight: 500; font-size: 13px; letter-spacing: 1px;
    color: var(--grey-text);
  }
  .contact { position: absolute; left: 34px; top: 208px; list-style: none; }
  .contact li {
    display: flex; align-items: center; gap: 9px;
    font-size: 13px; color: var(--grey-text); margin-bottom: 9px;
  }
  .contact svg { width: 12px; height: 12px; fill: var(--orange); flex: none; }
  .web-band {
    position: absolute; right: 0; bottom: 0;
    width: 18px; height: 150px; background: var(--orange);
  }
  .web {
    position: absolute; right: 34px; bottom: 26px;
    display: flex; align-items: center; gap: 7px;
    font-size: 12px; color: var(--grey-text);
  }
  .web svg { width: 11px; height: 11px; fill: var(--orange); }

  /* Back */
  .card-back {
    background: linear-gradient(135deg, var(--orange-light) 0%, var(--orange) 50%, var(--orange-deep) 100%);
    color: var(--white);
    display: flex; flex-direction: column; align-items: center; justify-content: center;
    text-align: center;
  }
  .back-decoration {
    position: absolute; left: 150px; top: 20px;
    width: 280px; height: 260px; border-radius: 50%;
    background: radial-gradient(circle, rgba(255,255,255,0.09) 0%, rgba(255,255,255,0.05) 55%, rgba(255,255,255,0) 70%);
  }
  .back-brand {
    position: relative; display: flex; align-items: center; gap: 12px;
  }
  .back-brand .brand-square { width: 20px; height: 20px; background: var(--white); }
  .back-brand .brand-name { color: var(--white); font-size: 38px; letter-spacing: 1px; }
  .tagline {
    position: relative; margin-top: 36px;
    font-weight: 500; font-size: 15px; letter-spacing: 0.3px;
  }
  .events {
    position: relative; margin-top: 8px;
    font-weight: 400; font-size: 15px; letter-spacing: 0.3px;
  }
</style>
</head>
<body>

  <section class="card card-front" aria-label="Business card front">
    <div class="front-decoration" role="img" aria-label="Faint brand decoration"></div>
    <div class="brand">
      <span class="brand-square"></span>
      <span class="brand-name">FALCRIDGE HIRES</span>
    </div>
    <div class="person">
      <p class="person-name">OWEN MARCHETTI</p>
      <p class="person-title">CEO</p>
    </div>
    <ul class="contact">
      <li>
        <svg viewBox="0 0 24 24" aria-hidden="true"><path d="M6.6 10.8a15.1 15.1 0 0 0 6.6 6.6l2.2-2.2c.3-.3.7-.4 1-.2 1.1.4 2.3.6 3.6.6.6 0 1 .4 1 1V20c0 .6-.4 1-1 1A17 17 0 0 1 3 4c0-.6.4-1 1-1h3.5c.6 0 1 .4 1 1 0 1.3.2 2.5.6 3.6.1.3 0 .7-.2 1z"/></svg>
        555 318-0476
      </li>
      <li>
        <svg viewBox="0 0 24 24" aria-hidden="true"><path d="M2 5h20v14H2zm2 2v.5l8 5 8-5V7l-8 5z"/></svg>
        owen@falcridgehires.com
      </li>
    </ul>
    <div class="web-band"></div>
    <div class="web">
      <svg viewBox="0 0 24 24" aria-hidden="true"><circle cx="12" cy="12" r="10"/></svg>
      www.falcridgehires.com
    </div>
  </section>

  <section class="card card-back" aria-label="Business card back">
    <div class="back-decoration" role="img" aria-label="Faint brand decoration"></div>
    <div class="back-brand">
      <span class="brand-square"></span>
      <span class="brand-name">FALCRIDGE HIRES</span>
    </div>
    <p class="tagline">Luxury Restroom Trailers Rental and Sales</p>
    <p class="events">Weddings | Concerts | Charity | Sporting | Corp</p>
  </section>

</body>
</html>
```